PillPeak website blog. Simple medical advice given in clear yes or no answers that save people money

I am developing a new web page that provides medical care cost savings at the consumers' fingertips. I need a web page that is clean, concise, and attractive for me to put my valuable medical information on. The information I provide is simple to obtain, yet very valuable to the consumer, and answered in a yes or no format. For example, A person may wonder if they need an antibiotic for cold like symptoms. Seeing a doctor for an antibiotic is very expensive. But with simple and clear advice at their fingertips, they can confidently avoid having to pay $200 or more to see a doctor and get an antibiotic. This is kind of like consumer reports for medical services.

Target Market(s)

People who are savvy shoppers and want to save money on healthcare. Likely younger ages between 21 and 60, who are mobile, readily use iphones, and want strong evidence based research to guide their decisions.

Industry/Entity Type

Coding

Number of Pages Required

Colors

Requirements
Must have
• A template on the "Question" and "Answer" page that can be edited many times that can be edited many times. The Confidence rating scale would need to be edited as well. The "Date Researched" the "PillPeak Pilluminate" and "References" all need to be able to be edited. This website must be very clear and simple to understand. A medical question is posed with a yes or no answer, then answered and given a confidence rating, we then tell them how much money they saved by going to our website.
Nice to have
• We want this to be slightly fun, vibrant, warm and inviting. This will be sometime later converted into an app format. Quirky, some humor to keep it interesting.
Should not have
• No sterile looking medical images. Not boring.

```html
<!DOCTYPE html>
<html lang="en">
<head>
<meta charset="utf-8">
<title>PillPeak – Clear Valuable Health Advice</title>
<link href="https://fonts.googleapis.com/css2?family=Ubuntu:wght@400;500;700&display=swap" rel="stylesheet">
<style>
  :root {
    --brand-red: #e2001a;
    --brand-blue: #1460b0;
    --navy: #0f2f66;
    --ink: #1c1c1c;
    --text: #222222;
    --muted: #3a3a3a;
    --panel: #1b1b1b;
    --bg-grey: #f3f3f3;
    --line: #dedede;
    --white: #ffffff;
  }
  * { box-sizing: border-box; margin: 0; padding: 0; }
  html, body { width: 1200px; height: 784px; overflow: hidden; }
  body {
    position: relative;
    background: var(--white);
    font-family: "Ubuntu", sans-serif;
    color: var(--text);
  }
  .grey-backdrop {
    position: absolute; left: 0; top: 0; width: 1200px; height: 461px;
    background: var(--bg-grey);
  }

  /* Header */
  .brand {
    position: absolute; left: 111px; top: 10px; width: 150px; height: 110px;
  }
  .brand-dot {
    position: absolute; left: 32px; top: 2px; width: 72px; height: 72px;
    border-radius: 50%; background: var(--brand-blue);
  }
  .brand-name {
    position: absolute; left: 2px; top: 76px;
    font-size: 32px; font-weight: 700; color: var(--brand-red); letter-spacing: 0.5px;
  }
  .tagline {
    position: absolute; left: 351px; top: 66px;
    font-size: 17.5px; font-weight: 700; color: var(--ink); letter-spacing: 0.3px;
  }
  .search {
    position: absolute; left: 884px; top: 63px; width: 216px; height: 29px;
    display: flex; background: var(--white); border: 1px solid var(--line);
  }
  .search-field {
    flex: 1; padding-left: 20px; line-height: 27px; font-size: 13.5px; color: var(--text);
  }
  .search-button {
    width: 38px; height: 29px; margin: -1px -1px 0 0; background: var(--brand-red);
    display: flex; align-items: center; justify-content: center;
  }

  /* Main navigation */
  .main-nav {
    position: absolute; left: 0; top: 144px; width: 1200px; height: 37px;
    background: var(--white); border-top: 1px solid var(--line); border-bottom: 1px solid var(--line);
  }
  .main-nav a {
    position: absolute; top: 0; height: 36px; line-height: 36px;
    font-size: 13.5px; color: var(--ink); text-decoration: none; text-transform: uppercase;
  }
  .main-nav a.is-active {
    background: var(--brand-blue); color: var(--white); padding: 0 17px; top: -1px; height: 37px; line-height: 38px;
  }

  /* Side menu */
  .side-menu {
    position: absolute; left: 111px; top: 207px; width: 251px; height: 391px;
    background: var(--panel); list-style: none;
  }
  .side-menu li {
    height: 55.8px; display: flex; align-items: center; padding-left: 24px;
    color: var(--white); font-size: 13.5px; text-transform: uppercase;
  }
  .side-menu li.is-active { background: var(--brand-red); }
  .side-menu svg { margin-right: 18px; }

  /* Hero */
  .hero {
    position: absolute; left: 369px; top: 207px; width: 719px; height: 391px; overflow: hidden;
  }
  .hero-photo {
    position: absolute; inset: 0;
    background: linear-gradient(100deg, #cfcac6 0%, #e9e7e4 30%, #f5f6f7 55%, #dfe6ee 80%, #c9d3dd 100%);
  }
  .hero-caption { position: absolute; left: 244px; top: 228px; width: 475px; height: 163px; }
  .hero-caption svg { position: absolute; inset: 0; }
  .hero-kicker {
    position: absolute; left: 57px; top: 20px; font-size: 20.5px; color: var(--white); text-transform: uppercase;
  }
  .hero-title {
    position: absolute; left: 57px; top: 47px; font-size: 31px; color: var(--white);
  }
  .hero-cta {
    position: absolute; left: 58px; top: 99px; width: 120px; height: 37px; line-height: 37px;
    background: var(--brand-blue); color: var(--white); font-size: 13.5px; text-align: center; border-radius: 2px;
  }
  .slider-dots { position: absolute; left: 30px; top: 358px; display: flex; gap: 10px; }
  .slider-dots span { width: 8px; height: 8px; border-radius: 50%; background: var(--white); }
  .slider-dots span.is-current { background: var(--brand-blue); }

  /* Footer */
  .legal { position: absolute; left: 120px; top: 623px; font-size: 10px; line-height: 20.5px; color: var(--text); letter-spacing: 0.4px; }
  .social { position: absolute; left: 122px; top: 675px; display: flex; gap: 5px; }
  .social span { width: 30px; height: 30px; border-radius: 3px; background: var(--brand-blue); }
  .social span.dark { background: var(--navy); }
  .social span.light { background: #1d8ce8; }

  .disclaimer { position: absolute; left: 373px; top: 619px; width: 470px; }
  .section-title { font-size: 13.5px; color: var(--ink); text-transform: uppercase; letter-spacing: 0.3px; }
  .disclaimer p { margin-top: 5px; padding-left: 2px; font-size: 9.8px; line-height: 20.5px; color: var(--muted); letter-spacing: 0.3px; }

  .join { position: absolute; left: 871px; top: 619px; width: 218px; }
  .email-field {
    margin-top: 9px; margin-left: 1px; width: 217px; height: 32px; line-height: 30px;
    border: 1px solid var(--line); border-radius: 4px; padding-left: 13px; font-size: 11px; color: var(--text);
  }
  .join .ask { margin-top: 20px; }
  .ask-button {
    margin-top: 8px; width: 206px; height: 33px; line-height: 33px; background: var(--brand-blue);
    color: var(--white); font-size: 13.5px; text-align: center; border-radius: 3px; letter-spacing: 0.3px;
  }
  .bottom-band { position: absolute; left: 0; top: 777px; width: 1200px; height: 7px; background: var(--brand-blue); }
</style>
</head>
<body>
  <div class="grey-backdrop"></div>

  <header>
    <div class="brand">
      <span class="brand-dot"></span>
      <span class="brand-name">PillPeak</span>
    </div>
    <div class="tagline">CLEAR VALUABLE - HEALTH ADVICE - RIGHT NOW</div>
    <div class="search">
      <span class="search-field">Search</span>
      <span class="search-button">
        <svg width="13" height="13" viewBox="0 0 13 13"><circle cx="5.3" cy="5.3" r="3.8" fill="none" stroke="#fff" stroke-width="2"/><line x1="8.2" y1="8.2" x2="11.8" y2="11.8" stroke="#fff" stroke-width="2.2" stroke-linecap="round"/></svg>
      </span>
    </div>
  </header>

  <nav class="main-nav">
    <a class="is-active" style="left:112px">Previous Screening</a>
    <a style="left:297px">Women’s Health</a>
    <a style="left:442px">Men’s Health</a>
    <a style="left:564px">Meds</a>
    <a style="left:629px">Surgery</a>
    <a style="left:716px">Imaging</a>
    <a style="left:798px">Peds</a>
    <a style="left:860px">Contact Us</a>
  </nav>

  <ul class="side-menu">
    <li class="is-active"><svg width="7" height="10" viewBox="0 0 7 10"><path d="M1.5 1.5 5 5 1.5 8.5" fill="none" stroke="#fff" stroke-width="2"/></svg>Who are we ?</li>
    <li><svg width="7" height="10" viewBox="0 0 7 10"><path d="M1.5 1.5 5 5 1.5 8.5" fill="none" stroke="#fff" stroke-width="2"/></svg>How it works?</li>
    <li><svg width="7" height="10" viewBox="0 0 7 10"><path d="M1.5 1.5 5 5 1.5 8.5" fill="none" stroke="#fff" stroke-width="2"/></svg>How we know</li>
    <li><svg width="7" height="10" viewBox="0 0 7 10"><path d="M1.5 1.5 5 5 1.5 8.5" fill="none" stroke="#fff" stroke-width="2"/></svg>Evidence based research</li>
    <li><svg width="7" height="10" viewBox="0 0 7 10"><path d="M1.5 1.5 5 5 1.5 8.5" fill="none" stroke="#fff" stroke-width="2"/></svg>Dr. Whitlow</li>
    <li><svg width="7" height="10" viewBox="0 0 7 10"><path d="M1.5 1.5 5 5 1.5 8.5" fill="none" stroke="#fff" stroke-width="2"/></svg>Who we are not</li>
    <li><svg width="7" height="10" viewBox="0 0 7 10"><path d="M1.5 1.5 5 5 1.5 8.5" fill="none" stroke="#fff" stroke-width="2"/></svg>Are we biased?</li>
  </ul>

  <section class="hero">
    <div class="hero-photo" role="img" aria-label="Photo of a young doctor in a white coat with a stethoscope working at a computer in a bright office"></div>
    <div class="slider-dots"><span></span><span class="is-current"></span><span></span></div>
    <div class="hero-caption">
      <svg width="475" height="163" viewBox="0 0 475 163"><polygon points="0,0 475,0 475,163 42,163" fill="#1b1b1b"/></svg>
      <div class="hero-kicker">Save $1000 per year on healthcare</div>
      <div class="hero-title">IT’S FREE</div>
      <div class="hero-cta">CLICK HERE</div>
    </div>
  </section>

  <footer>
    <div class="legal">© COPYRIGHTS 2018<br>WWW.COMPANYNAME.COM</div>
    <div class="social"><span class="dark"></span><span class="light"></span><span></span></div>

    <div class="disclaimer">
      <div class="section-title">Disclaimer</div>
      <p>Nor again is there anyone who loves or pursues or desires to obtain pain of itself, because it is pain, but because occasionally circumstances occur in which toil and pain can procure him some great pleasure. To take a trivial example, which of us .</p>
    </div>

    <div class="join">
      <div class="section-title">Become a PillPeak today!</div>
      <div class="email-field">Enter email</div>
      <div class="section-title ask">Ask a question here!</div>
      <div class="ask-button">if it is working well post it!</div>
    </div>
  </footer>

  <div class="bottom-band"></div>
</body>
</html>
```